Trifold for International Business Consulting firm

I have created a trifold piece (attached) that includes all the necessary information in a Word template; however, I need a professional that can make it look "current, international and modern". Our website, brightharborconsult.com, should give an idea as to the style and color template we like.
Industry/Entity Type
Business

```html
<!DOCTYPE html>
<html lang="en">
<head>
<meta charset="utf-8">
<title>Bright Harbor Consulting – Trifold Brochure</title>
<link rel="stylesheet" href="https://fonts.googleapis.com/css2?family=Open+Sans:wght@400;600;700&family=Ubuntu:wght@500;700&display=swap">
<style>
  :root{
    --stage:#e6e6e6;
    --paper:#f1f1f0;
    --paper-shade:#e7e7e5;
    --orange:#e8732a;
    --lime:#c6d94c;
    --lime-light:#e2ec9c;
    --ink:#3a3a3a;
    --ink-soft:#6f6f6f;
    --white:#ffffff;
  }
  *{box-sizing:border-box;margin:0;padding:0}
  html,body{width:1200px;height:1200px;overflow:hidden}
  body{background:var(--stage);font-family:"Open Sans",Arial,sans-serif;color:var(--ink);position:relative}

  .inside-spread{position:absolute;left:150px;top:28px;width:900px;height:660px;display:flex;box-shadow:0 6px 18px rgba(0,0,0,.12)}
  .panel{position:relative;width:300px;height:100%;background:linear-gradient(180deg,var(--paper),var(--paper-shade));
         padding:22px 18px 20px;border-top:6px solid var(--lime-light);border-bottom:12px solid var(--lime);
         font-size:10.4px;line-height:1.45}
  .panel + .panel{border-left:1px solid #d6d6d4}
  .panel p{margin-bottom:6px}

  .section-title{display:inline-block;background:var(--orange);color:var(--white);font-family:"Ubuntu",Arial,sans-serif;
         font-weight:700;font-size:13px;line-height:1.15;letter-spacing:.02em;text-transform:uppercase;padding:5px 10px 5px 8px;margin:4px 0 10px}
  .section-title.wide{display:block;margin-right:0}
  .key-term{font-weight:700}

  .dot-list{list-style:none;margin:8px 0 10px}
  .dot-list li{position:relative;padding-left:14px;margin-bottom:3px}
  .dot-list li::before{content:"";position:absolute;left:0;top:4px;width:8px;height:8px;border-radius:50%;background:var(--orange)}

  .offices{color:var(--ink-soft);margin-top:10px}
  .headquarters{text-align:center;font-weight:700;font-size:10.2px;line-height:1.35;margin-top:14px}
  .rights{font-weight:700;font-size:9.6px;margin-top:8px;text-align:center}

  .outside{position:absolute;top:722px;height:452px;width:205px;background:linear-gradient(180deg,var(--paper),var(--paper-shade));
         border-top:8px solid var(--lime);border-bottom:8px solid var(--lime);box-shadow:0 6px 16px rgba(0,0,0,.12);padding:38px 16px 20px}
  .cover{left:372px}
  .back-panel{left:623px}

  .brand{display:flex;align-items:center;gap:6px;font-family:"Open Sans",Arial,sans-serif;font-weight:700;color:var(--ink);
         font-size:15px;line-height:1.1;text-transform:uppercase;letter-spacing:.02em}
  .brand-mark{width:10px;height:10px;flex:none;background:var(--ink)}
  .brand-sub{font-size:9.6px;letter-spacing:.22em}

  .cover-lead{margin-top:58px;color:var(--ink-soft);font-size:10px;letter-spacing:.08em;text-transform:uppercase;line-height:1.5}
  .cover-headline{margin-top:22px;color:var(--orange);font-family:"Ubuntu",Arial,sans-serif;font-weight:700;font-size:14px;line-height:1.28;text-transform:uppercase}
  .cover-tagline{margin-top:26px;color:var(--ink-soft);font-size:9.4px;letter-spacing:.06em;text-transform:uppercase;line-height:1.6}

  .back-contact{margin-top:18px;font-size:10px;line-height:1.55;color:var(--ink)}
</style>
</head>
<body>

<section class="inside-spread" aria-label="Brochure inside spread">
  <article class="panel panel-expand">
    <h2 class="section-title">Should we expand?</h2>
    <p><span class="key-term">It depends:</span> Bright Harbor Consulting can assist you in an initial analysis to see if your company is prepared financially to expand and if the current infrastructure is adequate for international operations. We look at human resources, technology, operations, systems, processes and do a complete <span class="key-term">SWOT</span> analysis of your current operation.</p>
    <ul class="dot-list">
      <li>Have you maximized your current opportunities? Is your company mature for this endeavor?</li>
      <li>Have you discussed with all invested parties and taken all feedback into consideration?</li>
      <li>What are your short, mid and long term goals for growth?</li>
    </ul>
    <p>If you are not ready for international expansion today, we will design the path to help you get there.</p>
    <h2 class="section-title">How do we expand?</h2>
    <p>One of three ways:</p>
    <ul class="dot-list">
      <li>Green pasture organic growth: Evolve your current business internationally or create a new business from scratch.</li>
      <li>Joint Venture (JV) – partner with another entity in country of expansion.</li>
      <li>Merger or Acquisition (M&amp;A) – merge or acquire a new entity in country of expansion.</li>
    </ul>
  </article>

  <article class="panel panel-opportunity">
    <h2 class="section-title wide">Which expansion opportunity is best for my company?</h2>
    <p>Each opportunity has its own pros and cons for growth which can be largely dependent on the country of expansion and your budget. Some countries are business friendly for new business creation and growth while others are more optimal for international businesses to join, merge or acquire established companies in country.</p>
    <p>To determine the best way forward, it is good practice to seek counsel on your different options. Our networks specialize in all categories needed for international expansion, and our consultants coordinate with each specialist to work in unison for your best interest.</p>
    <h2 class="section-title wide">Working with specialists</h2>
    <p>We have spent years developing relationships with accounting, legal and financial specialists necessary for international growth. We have business associates located on both sides of the border, positioned for cost and time efficiencies and with the expertise you need to succeed in your growth plans.</p>
    <p>Instead of parading individual groups of specialists in front of you, each with its own sales pitch and service offerings, we introduce and manage the entire relationship and service. With a single point of contact and negotiated rates for your benefit, we keep your costs at an optimal level.</p>
  </article>

  <article class="panel panel-culture">
    <h2 class="section-title">Cultural management</h2>
    <p>In addition to international business consulting services, we have expertise in the cultural intricacies of international business and offer Crossway Culture Institute training.</p>
    <p>We have more than 20 years of experience consulting and training Global 500 companies, small and mid-size companies as well as individuals looking to improve their international business skills.</p>
    <p>There is significant evidence that cross-cultural training and knowledge lead to more successful international business relationships and they are key to success for mergers and acquisitions as well as joint ventures.</p>
    <p>“Your Success Drives our Success.” It is our goal to be a long term partner in your international growth strategies and development. Contact us today to get started.</p>
    <p class="offices">Offices in Houston, New York City, San Antonio, Monterrey, Guadalajara and Mexico City</p>
    <address class="headquarters">
      Headquarters<br>
      Bright Harbor Consulting<br>
      418 Lakeline Row<br>
      Suite 120<br>
      Austin, TX 78701<br>
      Phone (512) 555 - 0148<br>
      info@brightharborconsult.com<br>
      brightharborconsult.com
    </address>
    <p class="rights">©Meridian Service Partners, LLC</p>
  </article>
</section>

<section class="outside cover" aria-label="Brochure front cover">
  <div class="brand"><span class="brand-mark"></span><span>Bright Harbor</span></div>
  <div class="brand brand-sub" style="margin-left:16px;margin-top:3px">Consulting</div>
  <p class="cover-lead">Your international growth &amp; development process with us</p>
  <p class="cover-headline">Our effective, proven growth approach helps mid-size organizations accelerate and succeed in a global world</p>
  <p class="cover-tagline">Successful, low cost, low complexity, world class, cloud based business solutions</p>
</section>

<section class="outside back-panel" aria-label="Brochure back panel">
  <div class="brand"><span class="brand-mark"></span><span>Bright Harbor</span></div>
  <div class="brand brand-sub" style="margin-left:16px;margin-top:3px">Consulting</div>
  <address class="back-contact">
    418 Lakeline Row, Suite 120<br>
    Austin, TX 78701<br>
    Phone (512) 555-0148<br>
    brightharborconsult.com
  </address>
</section>

</body>
</html>
```